Redesign of the UI of a customer service platform

To improve the user experience of our customers, we need a new design for our agent interface of our customer service platform (velorant.com).
The focus will be on the dashboard and the inbox screens (see attached) along with the common UI elements (Buttons, menu, fonts, forms...)
We want a simple and distinctive design

Target Market(s)

Worldwide

Industry/Entity Type

It Service

Number of Pages Required

3 page

Font styles to use
Sans Serif

Requirements
Must have
• New Onboarding page: this is a new page that is shown to user the first time they login to the platform. This will replace the current onboarding screen (setup SMS, Setup widget...etc)
• Dashboard page: to access important information and activate services (see screenshot from current site)
• Inbox page: to manage all the interactions with customers. (see screenshot from current site)
• UI elements (buttons, menus, forms, tables, fonts, color palette)

```html
<!DOCTYPE html>
<html lang="en">
<head>
<meta charset="utf-8">
<title>velorant – Dashboard</title>
<link href="https://fonts.googleapis.com/css2?family=Open+Sans:wght@400;500;600&display=swap" rel="stylesheet">
<style>
:root{
  --sidebar:#1f1f1f;
  --sidebar-line:#2c2c2c;
  --sidebar-foot:#151515;
  --red:#e8302e;
  --green:#1aab1a;
  --blue:#1a6fe8;
  --yellow:#f6b616;
  --sky:#62b9e2;
  --page:#f7f7f7;
  --text:#222;
  --muted:#666;
  --line:#e2e2e2;
  --plan-bg:#efefef;
  --addon-bg:#e9f1f8;
  --addon-line:#9fcbe6;
}
*{box-sizing:border-box;margin:0;padding:0}
html,body{width:1200px;height:990px;overflow:hidden}
body{font-family:"Open Sans",sans-serif;background:var(--page);color:var(--text);position:relative;font-size:12px}
svg{display:block}
.topbar{position:absolute;left:0;top:0;width:1200px;height:56px;background:#fff}
.brand{position:absolute;left:38px;top:14px;display:flex;align-items:center;gap:6px;font-size:20px;font-weight:600;color:#222}
.brand .dot{width:18px;height:18px;border-radius:50%;background:#222}
.tool{position:absolute;top:18px}
.badge{position:absolute;background:var(--red);color:#fff;font-size:9px;border-radius:50%;width:14px;height:14px;text-align:center;line-height:14px}
.status{position:absolute;left:828px;top:19px;font-size:13px;font-weight:500;color:#333;display:flex;align-items:center;gap:8px}
.status i{width:7px;height:7px;border-radius:50%;background:var(--green)}
.user{position:absolute;left:947px;top:12px;display:flex;align-items:center;gap:12px;font-size:13px;font-weight:500;color:#333}
.avatar{width:31px;height:31px;border-radius:50%;background:linear-gradient(#c9b3a1,#8a7a70)}
.caret{color:#999;font-size:10px}
.sidebar{position:absolute;left:0;top:56px;width:194px;height:934px;background:var(--sidebar)}
.nav a{display:flex;align-items:center;height:48px;padding-left:36px;gap:14px;color:#fff;font-size:12.5px;text-decoration:none;border-bottom:1px solid var(--sidebar-line);position:relative}
.nav a.active{background:var(--red)}
.nav a.active::after{content:"";position:absolute;right:0;top:17px;border:7px solid transparent;border-right-color:var(--page)}
.nav .count{position:absolute;left:160px;width:15px;height:15px;border-radius:50%;background:var(--red);font-size:9px;text-align:center;line-height:15px}
.nav .chev{position:absolute;left:162px}
.feedback{position:absolute;left:0;bottom:0;width:194px;height:54px;background:var(--sidebar-foot);color:#fff;font-size:11.5px;font-weight:600;display:flex;align-items:center;justify-content:center;gap:10px}
.page-head{position:absolute;left:231px;top:56px;width:931px;height:49px;border-bottom:1px solid var(--line);display:flex;align-items:center;gap:20px}
.page-head h1{font-size:19px;font-weight:400;letter-spacing:.3px}
.head-action{position:absolute;right:0;top:10px;width:31px;height:31px;border-radius:50%;background:var(--red);display:flex;align-items:center;justify-content:center}
.stat{position:absolute;top:138px;width:216px;height:112px;background:#fff;border-top:2px solid;box-shadow:0 1px 4px rgba(0,0,0,.12);display:flex;align-items:center;padding-left:19px;gap:18px}
.stat .ring{width:54px;height:54px;border-radius:50%;display:flex;align-items:center;justify-content:center;flex:none}
.stat b{display:block;font-size:19px;font-weight:400;margin-bottom:6px}
.stat span{font-size:11px;color:#555;line-height:19px;display:block;white-space:nowrap}
.section-title{position:absolute;top:290px;font-size:16px;font-weight:400;border-bottom:1px solid var(--line);height:35px;width:456px;padding-left:1px}
.chart-head{position:absolute;left:232px;top:343px}
.chart-head h2{font-size:14.5px;font-weight:500;color:#333}
.chart-head p{font-size:11px;color:#555;margin-top:3px}
.chart-type{position:absolute;top:344px}
.chart-side{position:absolute;left:658px;top:346px;display:flex;flex-direction:column;gap:6px}
.chart-side div{width:28px;height:28px;border:1px solid #ddd;background:#fff;display:flex;align-items:center;justify-content:center}
.chart-side div.on{background:var(--green);border-color:var(--green)}
.chart{position:absolute;left:228px;top:396px}
.legend{position:absolute;left:366px;top:551px;display:flex;gap:16px;font-size:9.5px;font-weight:600}
.legend i{display:inline-block;width:12px;height:9px;margin-right:5px;vertical-align:-1px}
.plan{position:absolute;left:707px;top:346px;width:455px;height:126px;background:var(--plan-bg);border-left:3px solid var(--blue);padding:20px 0 0 20px}
.plan h3,.addon h3{font-size:15px;font-weight:400}
.plan h3 small{font-size:11px;color:#888}
.btn{position:absolute;right:18px;color:#fff;font-size:12px;font-weight:600;padding:0 11px;height:25px;display:flex;align-items:center;gap:6px;border-radius:2px}
.btn.green{background:var(--green)}
.btn.blue{background:var(--blue)}
.features{display:flex;gap:22px;margin-top:15px}
.feature{display:flex;align-items:center;gap:10px;position:relative}
.feature .ring{width:46px;height:46px;border-radius:50%;background:var(--red);display:flex;align-items:center;justify-content:center;flex:none}
.feature .ring em{position:absolute;left:32px;top:-2px;width:15px;height:15px;border-radius:50%;background:var(--red);border:1.5px solid #fff;color:#fff;font-size:8px;font-style:normal;text-align:center;line-height:12px}
.feature b{display:block;font-size:14px;font-weight:500}
.feature span{font-size:11.5px;color:#555}
.addon{position:absolute;left:707px;width:455px;background:var(--addon-bg);border-left:3px solid var(--addon-line);padding:20px 60px 0 20px}
.addon p{font-size:11px;color:#555;line-height:20px;margin-top:11px}
.footer{position:absolute;left:194px;top:935px;width:1006px;height:55px;background:#efefef;display:flex;align-items:center;padding-left:37px;font-size:10.5px;color:#666}
.footer .ver{position:absolute;right:58px;font-size:12px;color:#888}
</style>
</head>
<body>

<header class="topbar">
  <div class="brand"><i class="dot"></i>velorant</div>
  <div class="tool" style="left:721px">
    <svg width="22" height="20" viewBox="0 0 22 20"><path d="M3 9h5l1 2h4l1-2h5v8H3z M5 5h12l2 4" fill="#8a8a8a" stroke="#8a8a8a" stroke-width="1.5"/></svg>
    <span class="badge" style="left:-2px;top:-4px">4</span>
  </div>
  <div class="tool" style="left:775px">
    <svg width="20" height="20" viewBox="0 0 20 20"><path d="M11 2l7 7-9 9-7-7z" fill="#999"/><path d="M8 8l4 4" stroke="#fff" stroke-width="1.5"/></svg>
  </div>
  <div class="status"><i></i>Available <span class="caret">⌄</span></div>
  <div class="user"><div class="avatar" role="img" aria-label="Agent profile photo"></div>Noah Remy <span class="caret">⌄</span></div>
  <div class="tool" style="left:1097px">
    <svg width="17" height="17" viewBox="0 0 17 17"><circle cx="8.5" cy="8.5" r="8.5" fill="#999"/><text x="8.5" y="13" font-size="12" font-weight="700" fill="#fff" text-anchor="middle" font-family="Open Sans,sans-serif">?</text></svg>
  </div>
  <div class="tool" style="left:1145px;top:21px">
    <svg width="18" height="14" viewBox="0 0 18 14"><rect y="0" width="18" height="2.5" fill="#999"/><rect y="5.7" width="18" height="2.5" fill="#999"/><rect y="11.5" width="18" height="2.5" fill="#999"/></svg>
  </div>
</header>

<aside class="sidebar">
  <nav class="nav">
    <a class="active"><svg width="12" height="11" viewBox="0 0 12 11"><path d="M6 0l6 5.5h-2V11H7.5V7.5h-3V11H2V5.5H0z" fill="#fff"/></svg>DASHBOARD</a>
    <a><svg width="12" height="10" viewBox="0 0 12 10"><path d="M0 5h3.5l1 1.5h3l1-1.5H12v5H0zM2 0h8l2 4H8.5l-1 1.5h-3L3.5 4H0z" fill="#fff"/></svg>INBOX<span class="count">4</span></a>
    <a><svg width="12" height="12" viewBox="0 0 12 12"><path d="M7 0l5 5-7 7-5-5z" fill="#fff"/></svg>TICKETS</a>
    <a><svg width="14" height="11" viewBox="0 0 14 11"><circle cx="7" cy="3" r="2.6" fill="#fff"/><circle cx="2.5" cy="4" r="1.8" fill="#fff"/><circle cx="11.5" cy="4" r="1.8" fill="#fff"/><path d="M2.5 11c0-3 2-4.5 4.5-4.5s4.5 1.5 4.5 4.5zM0 10c0-2 1-3 2.5-3h1L2 10zM14 10c0-2-1-3-2.5-3h-1l1.5 3z" fill="#fff"/></svg>CLIENTS</a>
    <a><svg width="14" height="11" viewBox="0 0 14 11"><path d="M0 0v11h14v-1.5H1.5V0z" fill="#fff"/><rect x="3" y="5" width="2" height="4" fill="#fff"/><rect x="6" y="2" width="2" height="7" fill="#fff"/><rect x="9" y="4" width="2" height="5" fill="#fff"/></svg>REPORTS</a>
    <a><svg width="15" height="12" viewBox="0 0 15 12"><circle cx="5" cy="7" r="4" fill="none" stroke="#fff" stroke-width="2.4" stroke-dasharray="2 1.2"/><circle cx="11.5" cy="3.5" r="2.5" fill="none" stroke="#fff" stroke-width="1.8"/></svg>SETTINGS<span class="chev">›</span></a>
  </nav>
  <div class="feedback"><svg width="12" height="9" viewBox="0 0 12 9"><rect x=".6" y=".6" width="10.8" height="7.8" fill="none" stroke="#fff" stroke-width="1.2"/><path d="M.6.6L6 5l5.4-4.4" fill="none" stroke="#fff" stroke-width="1.2"/></svg>SEND FEEDBACK</div>
</aside>

<main>
  <div class="page-head">
    <svg width="17" height="15" viewBox="0 0 12 11"><path d="M6 0l6 5.5h-2V11H7.5V7.5h-3V11H2V5.5H0z" fill="#222"/></svg>
    <h1>DASHBOARD</h1>
    <div class="head-action"><svg width="12" height="13" viewBox="0 0 12 13"><circle cx="6" cy="3.5" r="3.2" fill="#fff"/><path d="M0 13c0-4 2.5-5.5 6-5.5s6 1.5 6 5.5z" fill="#fff"/></svg></div>
  </div>

  <section class="stat" style="left:231px;border-color:var(--green)">
    <div class="ring" style="background:var(--green)"><svg width="18" height="20" viewBox="0 0 12 13"><circle cx="6" cy="3.5" r="3.2" fill="#fff"/><path d="M0 13c0-4 2.5-5.5 6-5.5s6 1.5 6 5.5z" fill="#fff"/></svg></div>
    <div><b>0/0</b><span>TOTAL CLIENTS<br>SERVED / NON-SERVED</span></div>
  </section>
  <section class="stat" style="left:470px;border-color:var(--blue)">
    <div class="ring" style="background:var(--blue)"><svg width="24" height="24" viewBox="0 0 20 20"><path d="M11 2l7 7-9 9-7-7z" fill="none" stroke="#fff" stroke-width="2"/><path d="M8 8l4 4" stroke="#fff" stroke-width="1.6"/></svg></div>
    <div><b>0/0</b><span>CLIENT TICKETS<br>CLOSED/OPENED</span></div>
  </section>
  <section class="stat" style="left:707px;border-color:var(--yellow)">
    <div class="ring" style="background:var(--yellow)"><svg width="26" height="22" viewBox="0 0 26 22"><ellipse cx="10" cy="8" rx="9" ry="6.5" fill="none" stroke="#fff" stroke-width="2"/><path d="M17 12.5c3 .5 6 2 6 4.5 0 1-.5 2-1.5 2.7l1 2.3-3.5-1.5" fill="none" stroke="#fff" stroke-width="2"/></svg></div>
    <div><b>0/0</b><span>TOTAL CHAT MESSAGES</span></div>
  </section>
  <section class="stat" style="left:946px;border-color:var(--sky)">
    <div class="ring" style="background:var(--sky)"><svg width="24" height="20" viewBox="0 0 24 20"><ellipse cx="12" cy="8.5" rx="11" ry="8" fill="#fff"/><path d="M4 14l-2 5 6-3z" fill="#fff"/></svg></div>
    <div><b>0/0</b><span>TOTAL SMS MESSAGES</span></div>
  </section>

  <h2 class="section-title" style="left:230px">Report</h2>
  <h2 class="section-title" style="left:706px">Plan &amp; Add-ons</h2>

  <div class="chart-head">
    <h2>Clients total: served vs non-served (Account)</h2>
    <p>from 23 December 2016 to 07 january 2017</p>
  </div>
  <svg class="chart-type" style="left:575px" width="14" height="11" viewBox="0 0 14 11"><path d="M0 0v11h14v-1.5H1.5V0z" fill="#666"/><rect x="3" y="5" width="2" height="4" fill="#666"/><rect x="6" y="2" width="2" height="7" fill="#666"/><rect x="9" y="4" width="2" height="5" fill="#666"/></svg>
  <svg class="chart-type" style="left:603px" width="14" height="11" viewBox="0 0 14 11"><path d="M0 0v11h14" fill="none" stroke="#666" stroke-width="1.5"/><path d="M2 8l4-4 3 2 4-4" fill="none" stroke="#666" stroke-width="1.5"/></svg>

  <div class="chart-side">
    <div class="on"><svg width="11" height="12" viewBox="0 0 12 13"><circle cx="6" cy="3.5" r="3.2" fill="#fff"/><path d="M0 13c0-4 2.5-5.5 6-5.5s6 1.5 6 5.5z" fill="#fff"/></svg></div>
    <div><svg width="13" height="13" viewBox="0 0 20 20"><path d="M11 2l7 7-9 9-7-7z" fill="#555"/></svg></div>
    <div><svg width="14" height="12" viewBox="0 0 26 22"><ellipse cx="10" cy="8" rx="9" ry="6.5" fill="none" stroke="#555" stroke-width="2.4"/><path d="M17 12.5c3 .5 6 2 6 4.5 0 1-.5 2-1.5 2.7l1 2.3-3.5-1.5" fill="none" stroke="#555" stroke-width="2.4"/></svg></div>
    <div><svg width="13" height="11" viewBox="0 0 24 20"><ellipse cx="12" cy="8.5" rx="11" ry="8" fill="#555"/><path d="M4 14l-2 5 6-3z" fill="#555"/></svg></div>
  </div>

  <svg class="chart" width="420" height="140" viewBox="0 0 420 140" font-family="Open Sans,sans-serif" font-size="6" fill="#555">
    <text x="11" y="64" transform="rotate(-90 11 64)" text-anchor="middle" font-size="10" fill="#444">Clients</text>
    <g stroke="#e3e3e3" stroke-width="1">
      <line x1="34" y1="7" x2="410" y2="7"/><line x1="34" y1="30" x2="410" y2="30"/>
      <line x1="34" y1="52" x2="410" y2="52"/><line x1="34" y1="75" x2="410" y2="75"/>
      <line x1="34" y1="98" x2="410" y2="98"/><line x1="34" y1="121" x2="410" y2="121" stroke="#ccc"/>
    </g>
    <g text-anchor="end"><text x="26" y="9">5</text><text x="26" y="32">4</text><text x="26" y="54">3</text><text x="26" y="77">2</text><text x="26" y="100">1</text><text x="26" y="123">0</text></g>
    <g text-anchor="middle"><text x="71" y="132">24. Dec</text><text x="117" y="132">26. Dec</text><text x="163" y="132">28. Dec</text><text x="209" y="132">30. Dec</text><text x="256" y="132">1. Jan</text><text x="302" y="132">3. Jan</text><text x="348" y="132">5. Jan</text><text x="394" y="132">7. Jan</text></g>
  </svg>
  <div class="legend"><span><i style="background:#7cb5ec"></i>Served</span><span><i style="background:#434348"></i>Non-served</span></div>

  <section class="plan">
    <h3>Plan <small>(pro)</small></h3>
    <span class="btn green" style="top:17px">✔ Upgrade</span>
    <div class="features">
      <div class="feature"><div class="ring"><svg width="20" height="16" viewBox="0 0 14 11"><circle cx="7" cy="3" r="2.6" fill="#fff"/><circle cx="2.5" cy="4" r="1.8" fill="#fff"/><circle cx="11.5" cy="4" r="1.8" fill="#fff"/><path d="M2.5 11c0-3 2-4.5 4.5-4.5s4.5 1.5 4.5 4.5zM0 10c0-2 1-3 2.5-3h1L2 10zM14 10c0-2-1-3-2.5-3h-1l1.5 3z" fill="#fff"/></svg><em>1</em></div><div><b>Agents</b><span>Unlimited</span></div></div>
      <div class="feature"><div class="ring"><svg width="18" height="15" viewBox="0 0 18 15"><rect x="0" y="3" width="18" height="12" rx="1.5" fill="#fff"/><rect x="6" y="0" width="6" height="4" fill="none" stroke="#fff" stroke-width="1.6"/><line x1="4" y1="3" x2="4" y2="15" stroke="#e8302e"/><line x1="14" y1="3" x2="14" y2="15" stroke="#e8302e"/></svg><em>1</em></div><div><b>Departments</b><span>Unlimited</span></div></div>
      <div class="feature"><div class="ring"><svg width="16" height="16" viewBox="0 0 16 16"><path d="M3 0l3 4-2 2c1 2 3 4 6 6l2-2 4 3-2 3C7 16 0 9 0 3z" fill="#fff"/></svg><em>1</em></div><div><b>Phones</b><span>Unlimited</span></div></div>
    </div>
  </section>

  <section class="addon" style="top:487px;height:107px">
    <h3>Phones + SMS</h3>
    <span class="btn blue" style="top:17px">✔ Add photo</span>
    <p>Allow clients to send SMS messages right to your inbox. You may reply with SMS messages too</p>
  </section>
  <section class="addon" style="top:609px;height:85px">
    <h3>Paywell</h3>
    <span class="btn blue" style="top:17px">✔ Activate</span>
    <p>Receive one time payments with Paywell</p>
  </section>
  <section class="addon" style="top:709px;height:84px">
    <h3>Chatline</h3>
    <span class="btn blue" style="top:17px">✔ Activate</span>
    <p>Receive chat messages with Chatline</p>
  </section>
  <section class="addon" style="top:809px;height:84px">
    <h3>Friendnet</h3>
    <span class="btn blue" style="top:17px">✔ Activate</span>
    <p>Messenger Remove chat messages</p>
  </section>
</main>

<footer class="footer">Copyrights@2017Company Name , All rights Reserved<span class="ver">C15</span></footer>

</body>
</html>
```